Packaging for Hair Fibers Product

We are a start up company looking for a new packaging design for hair building fibers. These are aimed at predominantly men but also women as well. We already have a logo and i have the packaging design from our competitors. We are wanting to keep the look masculine as 90% of our users will be middle aged men. We would like the colours to be black and white but are open to other colours as well.
It will need to have our logo and the following somewhere on the front.
"Instant Fuller & Thicker Hair" & "Natural Hair Building Fibers" "28g" or "Net Weight 28g"
We only need the front of the packaging designed, please make the other sides of the packaging the same colour but blank.
Target Market(s)
Men 25+
Industry/Entity Type
Hair And Beauty
Requirements
Must have
- Logo which i have included. and the following somewhere on the front.
- "Instant Fuller & Thicker Hair" ; "Natural Hair Building Fibers" "28g" or "Net Weight 28g"
Nice to have
- Make it stand out from the competition or similar to the brisketto example.

```html
<!DOCTYPE html>
<html lang="en">
<head>
<meta charset="utf-8">
<title>Brisketto Hair Building Fibers – Packaging Fronts</title>
<link href="https://fonts.googleapis.com/css2?family=Questrial&family=Montserrat:wght@700&family=Great+Vibes&family=Knewave&display=swap" rel="stylesheet">
<style>
  :root {
    --stage: #555555;
    --box: #000000;
    --ink: #ffffff;
    --him-blue: #1aa6e8;
    --her-pink: #e6198a;
  }
  * { margin: 0; padding: 0; box-sizing: border-box; }
  html, body { width: 1200px; height: 1200px; overflow: hidden; background: var(--stage); }
  .canvas { position: relative; width: 1200px; height: 1200px; background: var(--stage); color: var(--ink); font-family: "Questrial", sans-serif; }
  .pack { position: absolute; top: 74px; height: 766px; background: var(--box); overflow: hidden; }
  .pack--him { left: 0; width: 402px; }
  .pack--core { left: 406px; width: 384px; }
  .pack--her { left: 794px; width: 406px; }
  .line { position: absolute; left: 0; width: 100%; text-align: center; line-height: 1; white-space: nowrap; }
  .line--tag { left: auto; width: auto; text-align: right; }
  .brand { font-family: "Questrial", sans-serif; letter-spacing: 8px; padding-left: 8px; }
  .brand-sub { font-family: "Questrial", sans-serif; letter-spacing: 6px; }
  .natural { font-family: "Great Vibes", cursive; }
  .headline { font-family: "Montserrat", sans-serif; font-weight: 700; letter-spacing: -1px; }
  .fibers-brush { font-family: "Knewave", sans-serif; }
  .fibers-script { font-family: "Great Vibes", cursive; color: var(--her-pink); }
  .claim { font-family: "Questrial", sans-serif; }
  .weight-label { font-family: "Questrial", sans-serif; }
  .weight-value { font-family: "Questrial", sans-serif; }
  .swoosh { position: absolute; left: 0; top: 0; width: 1200px; height: 1200px; pointer-events: none; }
  .caption { position: absolute; left: 0; top: 984px; width: 1200px; text-align: center; font-size: 42px; line-height: 1; }
  .caption .fibers-brush { color: var(--him-blue); font-size: 38px; }
</style>
</head>
<body>
<main class="canvas">

  <section class="pack pack--him" aria-label="For him pack front">
    <div class="line brand" style="top:81px;font-size:40px;">BRISKETTO</div>
    <div class="line line--tag brand-sub" style="top:122px;right:30px;font-size:16px;">FOR HIM</div>
    <div class="line natural" style="top:266px;font-size:56px;">Natural</div>
    <div class="line headline" style="top:316px;font-size:45px;">HAIR BUILDING</div>
    <div class="line fibers-brush" style="top:363px;font-size:46px;color:var(--him-blue);">FIBERS</div>
    <div class="line claim" style="top:486px;font-size:35px;">INSTANT FULLER</div>
    <div class="line claim" style="top:528px;font-size:35px;">&amp; THICKER HAIR</div>
    <div class="line weight-label" style="top:641px;font-size:26px;">Net Weight</div>
    <div class="line weight-value" style="top:669px;font-size:42px;">28g</div>
  </section>

  <section class="pack pack--core" aria-label="Core pack front">
    <div class="line brand" style="top:80px;font-size:50px;">BRISKETTO</div>
    <div class="line line--tag brand-sub" style="top:134px;right:22px;font-size:18px;">PRO</div>
    <div class="line natural" style="top:242px;font-size:54px;">Natural</div>
    <div class="line headline" style="top:288px;font-size:44px;">HAIR BUILDING</div>
    <div class="line fibers-brush" style="top:331px;font-size:46px;">FIBERS</div>
    <div class="line claim" style="top:480px;font-size:33px;">INSTANT FULLER</div>
    <div class="line claim" style="top:518px;font-size:33px;">&amp; THICKER HAIR</div>
    <div class="line weight-label" style="top:607px;font-size:26px;">Net Weight</div>
    <div class="line weight-value" style="top:633px;font-size:42px;">28g</div>
  </section>

  <section class="pack pack--her" aria-label="For her pack front">
    <div class="line brand" style="top:81px;font-size:48px;letter-spacing:7px;">BRISKETTO</div>
    <div class="line line--tag brand-sub" style="top:135px;right:6px;font-size:24px;letter-spacing:12px;">FOR HER</div>
    <div class="line natural" style="top:278px;font-size:56px;">Natural</div>
    <div class="line headline" style="top:327px;font-size:48px;">HAIR BUILDING</div>
    <div class="line fibers-script" style="top:380px;font-size:62px;">Fibers</div>
    <div class="line claim" style="top:507px;font-size:37px;">INSTANT FULLER</div>
    <div class="line claim" style="top:551px;font-size:37px;">&amp; THICKER HAIR</div>
    <div class="line weight-label" style="top:672px;font-size:27px;">Net Weight</div>
    <div class="line weight-value" style="top:700px;font-size:46px;">28g</div>
  </section>

  <svg class="swoosh" viewBox="0 0 1200 1200" aria-hidden="true">
    <path fill="var(--ink)" d="M406 736 C500 770 580 795 640 795 C700 790 750 770 790 754 L790 760 C740 775 690 795 620 797 L406 797 Z"/>
  </svg>

  <p class="caption">Rough blue “<span class="fibers-brush">FIBER</span>” word represents masculinity</p>

</main>
</body>
</html>
```